Industrial Company-Pop-Up Banner Design for Demolition and Infrastructure Company

Hi-
We need to create 2 pop-up banners for our company. They will both have the same logo, but different photos. We would like to have the colors white, red, and black and feature a modern design. I have attached some inspiration photos.

Target Market(s)

Trade Show/Job Fair Audience

Industry/Entity Type

construction, industrial

Font styles to use
Sans Serif

Colors
EB3D1F
EC4F4E
F09395
F8D3D4
FCEDEE

Requirements
Must have
• 2 versions, each with different photos but same design. Logo, Red, Black, and White Color Scheme, Modern Design
Nice to have
• Modern Design similar to the inspiration photos

```html
<!DOCTYPE html>
<html lang="en">
<head>
<meta charset="utf-8">
<title>Ironvale – Pop-Up Banners</title>
<link href="https://fonts.googleapis.com/css2?family=Encode+Sans+Condensed:wght@500;700&family=Kaushan+Script&display=swap" rel="stylesheet">
<style>
  :root {
    --page-bg: #eef1f5;
    --white: #ffffff;
    --red: #d0102a;
    --red-light: #e8535a;
    --script-red: #ec4f4e;
    --ink: #1c1d22;
  }
  html, body {
    margin: 0;
    padding: 0;
    width: 1200px;
    height: 900px;
    overflow: hidden;
    background: var(--page-bg);
  }
  .banner-pair {
    position: relative;
    width: 1200px;
    height: 900px;
  }
  .banner {
    position: absolute;
    top: 22px;
    width: 322px;
    height: 856px;
    box-shadow: 0 6px 24px rgba(20, 30, 50, 0.18);
    background: var(--white);
  }
  .banner--left { left: 230px; }
  .banner--right { left: 648px; }
  .banner svg { display: block; width: 100%; height: 100%; }

  .shape-white { fill: var(--white); }
  .shape-red { fill: var(--red); }
  .shape-red-light { fill: var(--red-light); }
  .shape-ink { fill: var(--ink); }
  .separator { stroke: var(--white); stroke-width: 7; stroke-linejoin: miter; }

  .headline {
    font-family: "Encode Sans Condensed", sans-serif;
    font-weight: 700;
    font-size: 60px;
    fill: var(--white);
    text-anchor: middle;
  }
  .headline-script {
    font-family: "Kaushan Script", cursive;
    font-size: 118px;
    fill: var(--script-red);
    text-anchor: middle;
  }
  .since {
    font-family: "Encode Sans Condensed", sans-serif;
    font-weight: 500;
    font-size: 40px;
    fill: var(--white);
    text-anchor: middle;
  }
  .brand-mark { fill: var(--red); }
  .brand-name {
    font-family: "Encode Sans Condensed", sans-serif;
    font-weight: 700;
    font-size: 28px;
    fill: var(--ink);
  }
</style>
</head>
<body>
<main class="banner-pair">

  <section class="banner banner--left" aria-label="Pop-up banner, version A">
    <svg viewBox="0 0 403 1070" xmlns="http://www.w3.org/2000/svg">
      <defs>
        <linearGradient id="a-photo-top" x1="0" y1="0" x2="0.6" y2="1">
          <stop offset="0" stop-color="#9fb8cf"/>
          <stop offset="0.45" stop-color="#c9a87a"/>
          <stop offset="1" stop-color="#8d3a2c"/>
        </linearGradient>
        <linearGradient id="a-photo-mid" x1="0" y1="0" x2="0" y2="1">
          <stop offset="0" stop-color="#3f86d6"/>
          <stop offset="0.45" stop-color="#8fbbe0"/>
          <stop offset="0.6" stop-color="#3f6a36"/>
          <stop offset="1" stop-color="#c79a72"/>
        </linearGradient>
        <linearGradient id="a-panel" x1="0" y1="0" x2="1" y2="1">
          <stop offset="0" stop-color="#17181c"/>
          <stop offset="1" stop-color="#5a5b5f"/>
        </linearGradient>
      </defs>

      <rect class="shape-white" width="403" height="1070"/>

      <polygon role="img" aria-label="Photo: excavator demolishing an industrial plant" fill="url(#a-photo-top)"
               points="0,0 128,0 283,160 0,445"/>
      <polygon class="shape-ink" points="128,16 200,16 164,52"/>
      <polygon role="img" aria-label="Photo: earthmoving trucks working a cleared site" fill="url(#a-photo-mid)" class="separator"
               points="300,180 403,288 403,605 230,432 152,345"/>
      <polygon class="shape-red separator" points="0,462 152,345 230,432 0,648"/>
      <polygon fill="url(#a-panel)" class="separator"
               points="0,648 230,432 403,605 403,985 318,1070 80,1070 0,990"/>
      <polygon class="shape-red-light" points="0,1005 0,1070 64,1070"/>
      <polygon class="shape-red" points="403,1000 403,1070 335,1070"/>

      <g class="brand">
        <rect class="brand-mark" x="262" y="89" width="14" height="14"/>
        <text class="brand-name" x="284" y="106">Ironvale</text>
      </g>

      <text class="headline" x="212" y="632">Shaping</text>
      <text class="headline" x="212" y="698">America’s</text>
      <text class="headline-script" x="208" y="820">skyline</text>
      <text class="since" x="215" y="940">since 1959</text>
    </svg>
  </section>

  <section class="banner banner--right" aria-label="Pop-up banner, version B">
    <svg viewBox="0 0 403 1070" xmlns="http://www.w3.org/2000/svg">
      <defs>
        <linearGradient id="b-photo-top" x1="1" y1="0" x2="0.3" y2="1">
          <stop offset="0" stop-color="#a7b7c4"/>
          <stop offset="0.35" stop-color="#5f7f4a"/>
          <stop offset="0.65" stop-color="#2f7fbf"/>
          <stop offset="1" stop-color="#9a9a8a"/>
        </linearGradient>
        <linearGradient id="b-photo-mid" x1="0" y1="0" x2="0.4" y2="1">
          <stop offset="0" stop-color="#3e78c8"/>
          <stop offset="0.35" stop-color="#d8dde3"/>
          <stop offset="0.7" stop-color="#c9a43a"/>
          <stop offset="1" stop-color="#7d7a70"/>
        </linearGradient>
        <linearGradient id="b-panel" x1="1" y1="0" x2="0" y2="1">
          <stop offset="0" stop-color="#17181c"/>
          <stop offset="1" stop-color="#5a5b5f"/>
        </linearGradient>
      </defs>

      <rect class="shape-white" width="403" height="1070"/>

      <g transform="translate(403,0) scale(-1,1)">
        <polygon role="img" aria-label="Photo: power station with stack and conveyors" fill="url(#b-photo-top)"
                 points="0,0 128,0 283,160 0,445"/>
        <polygon class="shape-ink" points="128,16 200,16 164,52"/>
        <polygon role="img" aria-label="Photo: excavator at a large assembly building" fill="url(#b-photo-mid)" class="separator"
                 points="300,180 403,288 403,605 230,432 152,345"/>
        <polygon class="shape-red separator" points="0,462 152,345 230,432 0,648"/>
        <polygon fill="url(#b-panel)" class="separator"
                 points="0,648 230,432 403,605 403,985 318,1070 80,1070 0,990"/>
        <polygon class="shape-red-light" points="0,1005 0,1070 64,1070"/>
        <polygon class="shape-red" points="403,1000 403,1070 335,1070"/>
      </g>

      <g class="brand">
        <rect class="brand-mark" x="24" y="89" width="14" height="14"/>
        <text class="brand-name" x="46" y="106">Ironvale</text>
      </g>

      <text class="headline" x="196" y="632">Shaping</text>
      <text class="headline" x="196" y="698">America’s</text>
      <text class="headline-script" x="196" y="820">skyline</text>
      <text class="since" x="196" y="940">since 1959</text>
    </svg>
  </section>

</main>
</body>
</html>
```